Ridgeline Journeys business card

please see website
www.ridgelinejourneys.comau

info needed on card
Curtis Halvey
Ph
email
Adventure Riding GPS trails

please use my logo and colours off my site

Curtis Halvey
curtis@ridgelinejourneys.com

```html
<!DOCTYPE html>
<html lang="en">
<head>
<meta charset="utf-8">
<title>Ridgeline Journeys business card</title>
<link rel="stylesheet" href="https://fonts.googleapis.com/css2?family=Arimo:wght@400;700&display=swap">
<style>
  :root {
    --stage: #222222;
    --card: #ffffff;
    --ink: #111111;
    --band: #050505;
    --accent: #f5d20f;
    --muted: #6b6b6b;
  }
  html, body {
    margin: 0;
    padding: 0;
    overflow: hidden;
  }
  body {
    width: 1200px;
    height: 750px;
    background: var(--stage);
    font-family: "Arimo", Arial, sans-serif;
    display: flex;
    flex-direction: column;
    align-items: center;
    justify-content: center;
    gap: 40px;
  }
  .card {
    position: relative;
    width: 525px;
    height: 300px;
    background: var(--card);
    box-shadow: 0 10px 30px rgba(0,0,0,0.5);
    overflow: hidden;
  }
  .brand-mark {
    display: flex;
    align-items: center;
    gap: 12px;
  }
  .brand-dot {
    width: 26px;
    height: 26px;
    border-radius: 50%;
    background: var(--accent);
    flex: none;
  }
  .brand-name {
    font-weight: 700;
    color: var(--ink);
    text-transform: uppercase;
    letter-spacing: 0.5px;
  }
  .tagline {
    color: var(--muted);
    font-size: 13px;
    letter-spacing: 0.3px;
  }

  /* Front */
  .card-front {
    display: flex;
    flex-direction: column;
    align-items: center;
    justify-content: center;
    gap: 14px;
  }
  .card-front .brand-name { font-size: 26px; }
  .card-front .brand-dot { width: 34px; height: 34px; }

  /* Back */
  .name-band {
    position: absolute;
    left: 0;
    right: 0;
    top: 38px;
    height: 66px;
    background: var(--band);
    border-top: 2px solid var(--accent);
    border-bottom: 2px solid var(--accent);
    box-shadow: 0 -6px 0 var(--card), 0 -8px 0 var(--accent), 0 6px 0 var(--card), 0 8px 0 var(--accent);
    display: flex;
    align-items: center;
    justify-content: center;
  }
  .person-name {
    color: var(--accent);
    font-size: 19px;
    font-weight: 700;
  }
  .back-brand {
    position: absolute;
    left: 0;
    right: 0;
    top: 140px;
    display: flex;
    flex-direction: column;
    align-items: center;
    gap: 8px;
  }
  .back-brand .brand-name { font-size: 22px; }
  .contact-line {
    position: absolute;
    left: 22px;
    right: 22px;
    bottom: 26px;
    display: flex;
    justify-content: center;
    gap: 10px;
    font-size: 11px;
    color: var(--muted);
    white-space: nowrap;
  }
  .contact-label {
    color: var(--accent);
    font-weight: 700;
    margin-right: 3px;
  }
</style>
</head>
<body>
  <section class="card card-front" aria-label="Card front">
    <div class="brand-mark">
      <span class="brand-dot"></span>
      <span class="brand-name">Ridgeline Journeys</span>
    </div>
    <p class="tagline">Adventure Riding GPS trails</p>
  </section>

  <section class="card card-back" aria-label="Card back">
    <div class="name-band">
      <span class="person-name">Curtis Halvey</span>
    </div>
    <div class="back-brand">
      <div class="brand-mark">
        <span class="brand-dot"></span>
        <span class="brand-name">Ridgeline Journeys</span>
      </div>
      <p class="tagline">Adventure Riding GPS trails</p>
    </div>
    <div class="contact-line">
      <span><span class="contact-label">P:</span>555 0142 8876</span>
      <span><span class="contact-label">E:</span>curtis@ridgelinejourneys.com</span>
      <span><span class="contact-label">W:</span>ridgelinejourneys.com.au</span>
    </div>
  </section>
</body>
</html>
```